Financial Advisor Resource Firm needs business card design

Need business card design for company in Omaha NE called Meridale Circle. We provide resources to financial advisors....workshop programs, retirement analysis, and insurance planning. I would like to see designs that use grays, greens, black, and white colors. The final design should communicate 'collaboration' and be simple yet attractive to financial planning clients. I will attached our logo and another picture of a puzzle piece coming together. I would like the incorporate the puzzle picture somehow, maybe on the back somehow, with color or just the gray scale....OR, the picture be the front of the card with 'Meridale' definition on it (see upload) and then company logo, employee name, title, address on the back (see ppt uploaded). The following disclosure needs to be included somewhere- Advisory services offered through Stonebrook Assets, LLC.
Updates

I uploaded a svg and ai file of the logo

Target Market(s)

Financial planning clients and financial advisors....so pretty diverse age range of about 40-70.

Industry/Entity Type

Financial Planning

Contact Information for Business Card

Tobias L. Fenwright, MBA
Founder/President
5287 E. Larkin Road
Suite 230
Omaha, NE 68190
Phone- (402) 555-0147
Cell- (402) 555-0183
Fax- (402) 555-0129
email- tobias@meridaleplan.example
web address- www.meridaleplan.example

Colors
1b1b1b
474747
d3d3d3
ffffff
9bcb3c
abd036

Requirements
Must have
• Must include logo provided, must be 2 sided, and must have disclosure...all of these items listed in project description

```html
<!DOCTYPE html>
<html lang="en">
<head>
<meta charset="utf-8">
<title>Meridale Circle – Business Card</title>
<link href="https://fonts.googleapis.com/css2?family=Roboto:wght@400;500&display=swap" rel="stylesheet">
<style>
  :root {
    --ink: #1b1b1b;
    --graphite: #474747;
    --mist: #d3d3d3;
    --paper: #ffffff;
    --leaf: #9bcb3c;
    --lime: #abd036;
    --backdrop: #e6e7e8;
  }
  * { box-sizing: border-box; margin: 0; padding: 0; }
  html, body {
    width: 1200px; height: 800px; overflow: hidden;
    background: var(--backdrop);
    font-family: "Roboto", Arial, sans-serif;
  }
  .sheet {
    width: 1200px; height: 800px;
    display: flex; align-items: center; justify-content: center; gap: 40px;
  }
  .card {
    position: relative;
    width: 520px; height: 297px;
    overflow: hidden;
    box-shadow: 0 2px 6px rgba(0,0,0,.12);
  }

  /* Back side */
  .card-back { background: var(--graphite); }
  .card-back .photo-area {
    position: absolute; inset: 0;
    background: radial-gradient(ellipse at 40% 55%, #a9a9a9 0%, #6e6e6e 45%, #2f2f2f 100%);
  }
  .card-back .brand-mark {
    position: absolute; left: 50%; top: 44%;
    transform: translate(-50%, -50%);
    display: flex; align-items: center; gap: 10px;
    color: var(--paper); font-weight: 500; font-size: 28px; letter-spacing: .5px;
    white-space: nowrap;
  }
  .brand-dot { width: 16px; height: 16px; border-radius: 50%; background: var(--leaf); }
  .card-back .disclosure {
    position: absolute; left: 26px; bottom: 40px;
    color: var(--leaf); font-size: 12px;
  }

  /* Front side */
  .card-front { background: var(--paper); }
  .card-front .brand {
    position: absolute; left: 200px; top: 40px;
    display: flex; align-items: center; gap: 10px;
    color: var(--ink); font-weight: 500; font-size: 28px; letter-spacing: .5px;
    white-space: nowrap;
  }
  .rule { position: absolute; height: 1px; background: var(--leaf); }
  .rule-top { left: 0; top: 102px; width: 300px; }
  .rule-bottom { left: 300px; top: 205px; width: 200px; }
  .contact-lines {
    position: absolute; left: 28px; top: 116px;
    list-style: none; color: var(--graphite); font-size: 11px; line-height: 15px;
  }
  .person { position: absolute; left: 250px; top: 118px; }
  .person-name { color: var(--leaf); font-weight: 500; font-size: 21px; }
  .person-title { color: var(--ink); font-size: 12.5px; margin-top: 3px; margin-left: 30px; }
  .address {
    position: absolute; right: 24px; top: 216px;
    text-align: right; font-style: normal;
    color: var(--graphite); font-size: 11px; line-height: 15px;
  }
</style>
</head>
<body>
<main class="sheet">
  <section class="card card-back" aria-label="Card back">
    <div class="photo-area" role="img" aria-label="Grayscale photograph of hands fitting puzzle pieces together"></div>
    <div class="brand-mark"><span class="brand-dot"></span>Meridale Circle</div>
    <p class="disclosure">Advisory services offered through Stonebrook Assets, LLC.</p>
  </section>

  <section class="card card-front" aria-label="Card front">
    <div class="brand"><span class="brand-dot"></span>Meridale Circle</div>
    <div class="rule rule-top"></div>
    <ul class="contact-lines">
      <li>(402) 555-0147 (P)</li>
      <li>(402) 555-0183 (M)</li>
      <li>(402) 555-0129 (F)</li>
      <li>tobias@meridaleplan.example</li>
    </ul>
    <div class="person">
      <p class="person-name">Tobias L. Fenwright, MBA</p>
      <p class="person-title">Founder/President</p>
    </div>
    <div class="rule rule-bottom"></div>
    <address class="address">
      5287 E. Larkin Road<br>
      Suite 230<br>
      Omaha, NE 68190<br>
      www.meridaleplan.example
    </address>
  </section>
</main>
</body>
</html>
```